Specialised investor in e-mobility and energy wants business card design

We need a business card design that fits our existing corporate design. <The look and feel must be 'sharp'/'clean', dynamic, communicate momentum, professionalism etc (as one would imagine from a firm in the financial sector). We like the idea of a reverse-side of the card that includes the logo, and the name and contact details on the other. We expect the deliverable to be whatever format might be required to be able to get cards printed directly by a service such as kelmo press. Our website is www.zub.capital

```html
<!DOCTYPE html>
<html lang="en">
<head>
<meta charset="utf-8">
<title>Zub Capital – Business Card</title>
<link rel="stylesheet" href="https://fonts.googleapis.com/css2?family=Arimo:wght@400;700&family=Questrial&display=swap">
<style>
  :root{
    --stage:#1f1f1f;
    --green-dark:#31501f;
    --green-light:#8ab34c;
    --paper:#ffffff;
    --card-w:560px;
    --card-h:320px;
  }
  *{box-sizing:border-box;margin:0;padding:0}
  html,body{width:1200px;height:1015px;overflow:hidden;background:var(--stage)}
  .stage{position:relative;width:1200px;height:1015px}
  .card{position:absolute;left:320px;width:var(--card-w);height:var(--card-h);overflow:hidden;box-shadow:0 10px 30px rgba(0,0,0,.6)}
  .card--back{top:120px;background:var(--green-dark)}
  .card--front{top:520px;background:var(--paper)}

  .band{position:absolute;left:0;right:0;top:205px;height:38px;background:var(--green-light)}
  .band__url{position:absolute;right:130px;top:11px;font:400 14px/1 Arimo,sans-serif;letter-spacing:1.5px;color:var(--paper)}

  .brand{position:absolute;display:flex;align-items:center;gap:12px;font-family:Questrial,sans-serif;font-weight:400;letter-spacing:1px}
  .brand__dot{width:18px;height:18px;border-radius:50%}
  .card--back .brand{left:0;right:0;top:95px;justify-content:center;font-size:52px;color:var(--paper)}
  .card--back .brand__dot{background:var(--paper)}
  .card--front .brand{left:38px;top:118px;font-size:40px;color:var(--green-dark)}
  .card--front .brand__dot{background:var(--green-dark)}

  .info-panel{position:absolute;top:0;right:0;bottom:0;width:48%;background:var(--green-dark)}
  .card--front .band{z-index:1}
  .card--front .band__url{right:110px}

  .contact{position:absolute;left:310px;top:34px;z-index:2;color:var(--paper);font-family:Arimo,sans-serif}
  .contact__name{font-weight:700;font-size:19px;letter-spacing:.5px;color:var(--green-light);text-transform:uppercase}
  .contact__role{font-size:14px;margin-top:2px}
  .contact__list{list-style:none;margin-top:18px;font-size:14px;line-height:20px}
  .contact__list li{display:flex;align-items:center;gap:7px}
  .contact__list svg{width:14px;height:14px;flex:none}
  .contact__address{margin-top:12px;font-size:14px;line-height:18px}
</style>
</head>
<body>
<main class="stage">
  <section class="card card--back" aria-label="Card reverse">
    <div class="brand"><span class="brand__dot"></span>Zub Capital</div>
    <div class="band"><span class="band__url">www.websitename.com</span></div>
  </section>

  <section class="card card--front" aria-label="Card front">
    <div class="info-panel"></div>
    <div class="brand"><span class="brand__dot"></span>Zub Capital</div>
    <div class="contact">
      <h1 class="contact__name">Marcus Hale</h1>
      <p class="contact__role">Managing Director</p>
      <ul class="contact__list">
        <li>
          <svg viewBox="0 0 24 24" aria-hidden="true"><path fill="#8ab34c" d="M6.6 10.8a15 15 0 0 0 6.6 6.6l2.2-2.2a1 1 0 0 1 1-.25 11.4 11.4 0 0 0 3.6.57 1 1 0 0 1 1 1V20a1 1 0 0 1-1 1A17 17 0 0 1 3 4a1 1 0 0 1 1-1h3.5a1 1 0 0 1 1 1c0 1.25.2 2.45.57 3.57a1 1 0 0 1-.25 1z"/></svg>
          044-123 456 789
        </li>
        <li>
          <svg viewBox="0 0 24 24" aria-hidden="true"><path fill="#8ab34c" d="M2 5h20v14H2z"/><path fill="none" stroke="#31501f" stroke-width="1.8" d="M2 5l10 8 10-8"/></svg>
          info@webname.com
        </li>
      </ul>
      <p class="contact__address">421, Address line goes here<br>45452, Country Name</p>
    </div>
    <div class="band"><span class="band__url">www.websitename.com</span></div>
  </section>
</main>
</body>
</html>
```